Gobal construction supply company needs new business card design

I need a business card design for my global supply company using an existing logo. i will be looking to print these on rounded corner cards with the black background version of my logo on the back. on the front white background, my logo again and my simple details.

```html
<!DOCTYPE html>
<html lang="en">
<head>
<meta charset="utf-8">
<title>Meridian Build Supply — Business Card</title>
<link rel="stylesheet" href="https://fonts.googleapis.com/css2?family=Arimo:wght@400;700&display=swap">
<style>
  :root {
    --backdrop: #dedede;
    --ink: #000000;
    --card-dark: #1c1c1c;
    --paper: #f4f4f4;
    --accent: #e00000;
    --white: #f5f5f5;
    --text-main: #111111;
    --text-soft: #555555;
    --stripe-grey: #8a8a8a;
  }
  * { margin: 0; padding: 0; box-sizing: border-box; }
  html, body { width: 1200px; height: 960px; overflow: hidden; }
  body {
    background: var(--backdrop);
    font-family: "Arimo", Arial, sans-serif;
    position: relative;
  }
  .card {
    position: absolute;
    width: 600px;
    height: 343px;
    border-radius: 18px;
    overflow: hidden;
  }
  /* Front */
  .card-front { left: 186px; top: 113px; background: var(--paper); }
  .front-brand-panel {
    position: absolute; left: 0; top: 0; width: 270px; height: 100%;
    background: var(--ink);
    display: flex; align-items: center; justify-content: center; gap: 10px;
  }
  .brand-name {
    font-weight: 700; color: var(--white); letter-spacing: 1px;
  }
  .front-brand-panel .brand-name { font-size: 30px; }
  .brand-dot {
    width: 22px; height: 22px; border-radius: 50%; background: var(--accent);
    flex: none;
  }
  .divider-stripe {
    position: absolute; left: 271px; top: 0; width: 11px; height: 100%;
  }
  .divider-stripe .seg-red { position: absolute; left: 0; width: 100%; background: var(--accent); }
  .divider-stripe .seg-top { top: 0; height: 60px; }
  .divider-stripe .seg-bottom { bottom: 0; height: 58px; }
  .divider-stripe .seg-mid {
    position: absolute; left: 0; width: 100%; top: 60px; bottom: 58px;
    background: var(--stripe-grey);
  }
  .contact-block {
    position: absolute; left: 307px; top: 70px; color: var(--text-soft);
    font-size: 14px; line-height: 18px;
  }
  .person-name { font-size: 21px; font-weight: 700; color: var(--text-main); line-height: 22px; letter-spacing: 0.3px; }
  .person-role { font-size: 14px; font-weight: 700; color: var(--accent); line-height: 18px; }
  .rule { width: 54px; height: 1px; background: var(--accent); margin: 10px 0 12px; }
  /* Back */
  .card-back {
    left: 434px; top: 511px; background: var(--card-dark);
    display: flex; align-items: center; justify-content: center; gap: 12px;
  }
  .card-back .brand-name { font-size: 26px; }
</style>
</head>
<body>
  <section class="card card-front" aria-label="Business card front">
    <div class="front-brand-panel">
      <span class="brand-name">MERIDIAN</span>
      <span class="brand-dot"></span>
    </div>
    <div class="divider-stripe">
      <span class="seg-red seg-top"></span>
      <span class="seg-mid"></span>
      <span class="seg-red seg-bottom"></span>
    </div>
    <div class="contact-block">
      <p class="person-name">DANIEL HART</p>
      <p class="person-role">CEO/FOUNDER</p>
      <div class="rule"></div>
      <p>4120 Larkspur Road</p>
      <p>Fairbanks, Alaska 29810</p>
      <div class="rule"></div>
      <p>512 -304 -7716</p>
      <p>947 -215 -6083</p>
      <div class="rule"></div>
      <p>daniel@meridianbuildsupply.com</p>
      <p>www.meridianbuildsupply.com</p>
    </div>
  </section>

  <section class="card card-back" aria-label="Business card back">
    <span class="brand-name">MERIDIAN BUILD SUPPLY</span>
    <span class="brand-dot"></span>
  </section>
</body>
</html>
```